Business card design Needed for new logo / Construction business, home extensions and new builds

We need a business card design using our new logo files which i will attach to this project :)

We are a small construction business specialising in home extensions, new builds and property development. We are very ambitious and would appreciate professional and elegant designs for our new business card.

Very serious about using the services on MakerQuarry and recently acquired our new logo from here :)

Please get involved, i will feedback when i can as i am very busy but can respond daily, thanks

Target Market(s)

People that want to build onto their houses, new building developments or adding too their existing property

Industry/Entity Type

Construction

Contact Information for Business Card

Renwick Tolliver Construction, Lionel Ashby (Managing Director), Tel 07822254961, email - info@renwick-tolliver, www.renwick-tolliver.co.uk

Colors

Designer to choose colors to be used in the design.

Requirements
Must have
• I like a deep grey on the back please. A lot of you have provided black from and back, try mixing things up a little. The black looks cool 😎 Thanks

```html
<!DOCTYPE html>
<html lang="en">
<head>
<meta charset="utf-8">
<title>Renwick Tolliver Construction – Business Card</title>
<link rel="stylesheet" href="https://fonts.googleapis.com/css2?family=Open+Sans:wght@400;600;700&display=swap">
<style>
  :root {
    --bg: #232323;
    --card: #1f1f23;
    --gold: #d9a431;
    --gold-light: #f1c45a;
    --gold-deep: #b9821f;
    --silver: #c9cacc;
    --text: #f2f2f2;
  }
  * { margin: 0; padding: 0; box-sizing: border-box; }
  html, body { width: 1200px; height: 780px; overflow: hidden; background: var(--bg); }
  body { font-family: "Open Sans", Arial, sans-serif; color: var(--text); position: relative; }

  .card {
    position: absolute;
    top: 135px;
    width: 330px;
    height: 510px;
    background: var(--card);
    border-radius: 18px;
    border: 2px solid var(--gold);
    box-shadow: 0 18px 40px rgba(0,0,0,0.55);
    overflow: hidden;
  }
  .card--front { left: 225px; }
  .card--back  { left: 645px; }

  /* Front: brand name set vertically */
  .front-brand {
    position: absolute;
    left: 50%; top: 50%;
    transform: translate(-50%, -50%) rotate(-90deg);
    display: flex; align-items: center; gap: 14px;
    white-space: nowrap;
  }
  .brand-mark { width: 22px; height: 22px; background: var(--gold); flex: none; }
  .brand-name {
    font-weight: 600; color: var(--gold);
    text-transform: uppercase; letter-spacing: 2px; line-height: 1.3;
  }
  .front-brand .brand-name { font-size: 20px; }

  /* Back */
  .back-brand {
    position: absolute; top: 62px; left: 0; right: 0;
    display: flex; flex-direction: column; align-items: center; gap: 14px;
    text-align: center;
  }
  .back-brand .brand-mark { width: 34px; height: 34px; }
  .back-brand .brand-name { font-size: 15px; }

  .person { position: absolute; left: 34px; top: 262px; }
  .person-name { font-size: 26px; font-weight: 700; line-height: 1; }
  .person-name .first { color: var(--silver); }
  .person-name .last { color: var(--gold); }
  .person-role { font-size: 12px; font-weight: 600; margin-top: 4px; padding-left: 62px; }

  .dot-row { position: absolute; left: 14px; width: 300px; height: 26px; }
  .dot-row--contact { top: 318px; }
  .dot-row--address { top: 428px; }

  .contact-list {
    position: absolute; left: 112px; top: 350px;
    list-style: none; font-size: 12.5px; line-height: 19px;
  }
  .address {
    position: absolute; left: 112px; top: 460px;
    font-style: normal; font-size: 12.5px; line-height: 19px;
  }
</style>
</head>
<body>

<section class="card card--front" aria-label="Card front">
  <div class="front-brand">
    <span class="brand-mark"></span>
    <span class="brand-name">Renwick Tolliver<br>Construction</span>
  </div>
</section>

<section class="card card--back" aria-label="Card back">
  <div class="back-brand">
    <span class="brand-mark"></span>
    <span class="brand-name">Renwick Tolliver<br>Construction</span>
  </div>

  <div class="person">
    <p class="person-name"><span class="first">Lionel</span> <span class="last">Ashby</span></p>
    <p class="person-role">Managing Director</p>
  </div>

  <svg class="dot-row dot-row--contact" viewBox="0 0 300 26" aria-hidden="true">
    <g fill="var(--gold)">
      <circle cx="6" cy="13" r="2"/><circle cx="16" cy="13" r="2.5"/><circle cx="28" cy="13" r="3"/>
      <circle cx="41" cy="13" r="3.6"/><circle cx="56" cy="13" r="4.2"/><circle cx="72" cy="13" r="4.8"/>
      <circle cx="89" cy="13" r="5.4"/>
    </g>
    <g>
      <circle cx="112" cy="13" r="11" fill="var(--gold)"/>
      <path d="M107 8 q-1 6 5 11 l3-2.5 -3-3 -1.6 1.2 q-2-2-2.6-4.4 l1.6-1 -1.4-3.6z" fill="#1f1f23"/>
      <circle cx="138" cy="13" r="11" fill="var(--gold)"/>
      <rect x="132" y="8.5" width="12" height="9" fill="none" stroke="#1f1f23" stroke-width="1.5"/>
      <path d="M132 8.5 l6 5 6-5" fill="none" stroke="#1f1f23" stroke-width="1.5"/>
      <circle cx="164" cy="13" r="11" fill="var(--gold)"/>
      <circle cx="164" cy="13" r="6" fill="none" stroke="#1f1f23" stroke-width="1.5"/>
      <path d="M158 13 h12 M164 7 q-3.5 6 0 12 q3.5-6 0-12" fill="none" stroke="#1f1f23" stroke-width="1.2"/>
    </g>
    <g fill="var(--gold)">
      <circle cx="189" cy="13" r="5.4"/><circle cx="205" cy="13" r="4.8"/><circle cx="220" cy="13" r="4.2"/>
      <circle cx="234" cy="13" r="3.6"/><circle cx="247" cy="13" r="3"/><circle cx="259" cy="13" r="2.5"/>
      <circle cx="270" cy="13" r="2"/><circle cx="280" cy="13" r="1.6"/>
    </g>
  </svg>

  <ul class="contact-list">
    <li>0782 225 4961</li>
    <li>info@renwick-tolliver.co.uk</li>
    <li>www.renwick-tolliver.co.uk</li>
  </ul>

  <svg class="dot-row dot-row--address" viewBox="0 0 300 26" aria-hidden="true">
    <g fill="var(--gold)">
      <circle cx="6" cy="13" r="2"/><circle cx="16" cy="13" r="2.5"/><circle cx="28" cy="13" r="3"/>
      <circle cx="41" cy="13" r="3.6"/><circle cx="56" cy="13" r="4.2"/><circle cx="72" cy="13" r="4.8"/>
      <circle cx="89" cy="13" r="5.4"/><circle cx="107" cy="13" r="5.8"/><circle cx="126" cy="13" r="6"/>
    </g>
    <circle cx="150" cy="13" r="11" fill="var(--gold)"/>
    <path d="M150 20 q-5-5.5-5-9 a5 5 0 0 1 10 0 q0 3.5-5 9z" fill="#1f1f23"/>
    <circle cx="150" cy="11" r="1.8" fill="var(--gold)"/>
    <g fill="var(--gold)">
      <circle cx="174" cy="13" r="6"/><circle cx="193" cy="13" r="5.8"/><circle cx="211" cy="13" r="5.4"/>
      <circle cx="228" cy="13" r="4.8"/><circle cx="243" cy="13" r="4.2"/><circle cx="257" cy="13" r="3.6"/>
      <circle cx="269" cy="13" r="3"/><circle cx="280" cy="13" r="2.5"/><circle cx="290" cy="13" r="2"/>
    </g>
  </svg>

  <address class="address">
    Hollin Lane, Ashcombe<br>
    Marlbury, MR4 7QT
  </address>
</section>

</body>
</html>
```